Firm Stationery Design

I need a design for stationery, including: Stationery First Page, Stationery Second Sheet, Envelope, Mailing Label for Flat Envelopes, and Business Cards

```html
<!DOCTYPE html>
<html lang="en">
<head>
<meta charset="UTF-8">
<title>Harlow Law LLC – Envelope</title>
<link href="https://fonts.googleapis.com/css2?family=Montserrat:wght@300;400;800&display=swap" rel="stylesheet">
<style>
  :root {
    --backdrop: #3a3a3a;
    --paper: #ffffff;
    --ink: #1a1a1a;
    --accent: #f39a1e;
    --window-light: #f7f7f7;
    --window-mid: #e4e4e4;
    --window-dark: #cfcfcf;
  }
  html, body {
    margin: 0;
    padding: 0;
    width: 1200px;
    height: 800px;
    overflow: hidden;
    background: var(--backdrop);
    font-family: "Montserrat", sans-serif;
  }
  .envelope {
    position: absolute;
    left: 120px;
    top: 160px;
    width: 960px;
    height: 480px;
    background: var(--paper);
    box-shadow: 0 18px 40px rgba(0, 0, 0, 0.45);
  }
  .sender {
    position: absolute;
    left: 46px;
    top: 42px;
    display: flex;
    align-items: flex-end;
    gap: 26px;
  }
  .brand {
    display: flex;
    flex-direction: column;
    align-items: flex-start;
  }
  .brand-square {
    width: 40px;
    height: 40px;
    margin-left: 40px;
    margin-bottom: 12px;
    background: var(--accent);
  }
  .brand-name {
    margin: 0;
    font-weight: 800;
    color: var(--ink);
    text-transform: uppercase;
    line-height: 1;
  }
  .brand-name-main {
    display: block;
    font-size: 25px;
    letter-spacing: 0.3px;
  }
  .brand-name-sub {
    display: block;
    margin-top: 6px;
    font-size: 10px;
    letter-spacing: 7.4px;
  }
  .divider {
    width: 1.5px;
    height: 58px;
    margin-bottom: 2px;
    background: var(--accent);
  }
  .return-address {
    font-style: normal;
    font-weight: 400;
    font-size: 14px;
    line-height: 1.3;
    color: var(--ink);
    margin-bottom: 2px;
  }
  .address-window {
    position: absolute;
    right: 130px;
    bottom: 78px;
    width: 270px;
    height: 118px;
    background: linear-gradient(90deg, var(--window-dark) 0%, var(--window-mid) 40%, var(--window-light) 62%, var(--paper) 68%, var(--window-mid) 82%, var(--window-dark) 100%);
  }
</style>
</head>
<body>
  <main class="envelope">
    <header class="sender">
      <div class="brand">
        <span class="brand-square"></span>
        <p class="brand-name">
          <span class="brand-name-main">Harlow</span>
          <span class="brand-name-sub">Law LLC</span>
        </p>
      </div>
      <span class="divider"></span>
      <address class="return-address">
        Your address, City<br>
        State, Zip 1234
      </address>
    </header>
    <div class="address-window"></div>
  </main>
</body>
</html>
```